Business Cards for new orthopaedic surgery practice

My husband and I are starting our own orthopaedic surgery practice. We are looking for a business card that is uniform, but one will have my name/title and the other will have his. You can just create one design with my name on it for now. But when I choose your design as the winning design I will ask that you add another copy with his name/title.

We are looking for classy, simple, elite all in one. We like dark blues/a little gold/yellow. Something that goes with our logo. We want our logo incorporated. Here is all the info you need:
Business name: RV Bone & Vitality Center
Location: 38517 North Willowmere Ave
Maple Hollow, FL 33990
Phone: 954-218-4063
Fax: 954-582-7341
Email: info@myrvbonecare.example

Names: Lydia Vance, M.D.
Board Certified Hand and Upper Extremity Surgeon

Ebo Dansu, M.D.
Board Certified Hip & Knee Replacement/General Orthopaedic Surgeon

Can decide what you want to put on the back. Maybe a slogan:
Steady Hands. Stronger Every Day

I am just going to upload our logo. The only thing is if we select you as the winning design, the location, and phone numbers may change. We will need your help to update that once fully solidified.

Industry/Entity Type

Medical

Contact Information for Business Card

Colors
0054AA
0677BA
7BADD7
CADEEF
E8F1F8
0094D4
00A9DD
6FCCEA
C7EBF8
E9F6FB

Requirements
Must have
• class, appeal,
Should not have
• We want to air on the side of masculine if we are looking at masculine vs. feminine feel. But we still want it classy, sophisticated, and something we will love

```html
<!DOCTYPE html>
<html lang="en">
<head>
<meta charset="utf-8">
<title>RV Bone &amp; Vitality Center – Business Card</title>
<link href="https://fonts.googleapis.com/css2?family=Playfair+Display:wght@600&family=Poppins:wght@400;500&display=swap" rel="stylesheet">
<style>
  :root {
    --navy: #1b2a4e;
    --gold: #c49a55;
    --ink: #1e2236;
    --paper: #ffffff;
    --backdrop: #e6e7eb;
  }
  * { margin: 0; padding: 0; box-sizing: border-box; }
  html, body { width: 1200px; height: 900px; overflow: hidden; }
  body {
    background: var(--backdrop);
    font-family: "Poppins", sans-serif;
    color: var(--ink);
    position: relative;
  }
  .card {
    position: absolute;
    left: 250px;
    width: 700px;
    height: 400px;
    border-radius: 26px;
    overflow: hidden;
    box-shadow: 0 10px 30px rgba(20, 30, 60, 0.18);
  }
  /* Back side */
  .card--back {
    top: 35px;
    background: var(--navy);
    color: var(--paper);
  }
  .card--back .brand {
    position: absolute;
    left: 50%;
    top: 50px;
    transform: translateX(-50%);
    width: 230px;
    height: 230px;
    border: 2px solid var(--paper);
    border-radius: 50%;
    display: flex;
    align-items: center;
    justify-content: center;
    text-align: center;
  }
  .brand-name {
    font-family: "Playfair Display", serif;
    font-weight: 600;
    font-size: 26px;
    line-height: 1.2;
    letter-spacing: 1px;
    padding: 0 24px;
  }
  .card--back .slogan {
    position: absolute;
    left: 0; right: 0;
    top: 318px;
    text-align: center;
    font-size: 17px;
    letter-spacing: 0.5px;
  }
  /* Front side */
  .card--front {
    top: 465px;
    background: var(--paper);
  }
  .doctors {
    position: absolute;
    left: 48px;
    top: 40px;
    width: 340px;
  }
  .doctor + .doctor { margin-top: 12px; }
  .doctor-name {
    font-family: "Playfair Display", serif;
    font-weight: 600;
    color: var(--gold);
    font-size: 25px;
    line-height: 1.15;
  }
  .doctor-title {
    font-size: 14.5px;
    line-height: 1.3;
    color: var(--ink);
  }
  .divider {
    position: absolute;
    left: 48px;
    right: 40px;
    top: 250px;
    height: 1.5px;
    background: var(--navy);
  }
  .contacts {
    position: absolute;
    left: 48px;
    top: 264px;
    list-style: none;
    font-size: 15px;
    line-height: 1.55;
  }
  .contacts li { display: flex; align-items: center; gap: 10px; }
  .contacts svg { width: 14px; height: 14px; fill: var(--gold); flex: none; }
  .card--front .brand {
    position: absolute;
    left: 470px;
    top: 40px;
    width: 190px;
    height: 190px;
    border: 2px solid var(--navy);
    border-radius: 50%;
    display: flex;
    align-items: center;
    justify-content: center;
    text-align: center;
    color: var(--navy);
  }
  .card--front .brand .brand-name { font-size: 22px; padding: 0 18px; }
  .address-band {
    position: absolute;
    left: 0; right: 0; bottom: 0;
    height: 92px;
  }
  .address-band svg { position: absolute; inset: 0; width: 100%; height: 100%; }
  .address {
    position: absolute;
    left: 455px;
    top: 24px;
    color: var(--paper);
    font-size: 15.5px;
    line-height: 1.4;
    font-style: normal;
    white-space: nowrap;
  }
</style>
</head>
<body>

  <section class="card card--back" aria-label="Card back">
    <div class="brand">
      <span class="brand-name">RV Bone &amp; Vitality Center</span>
    </div>
    <p class="slogan">Steady Hands. Stronger Every Day</p>
  </section>

  <section class="card card--front" aria-label="Card front">
    <div class="doctors">
      <div class="doctor">
        <h2 class="doctor-name">Lydia Vance, M.D.</h2>
        <p class="doctor-title">Board Certified Hand and<br>Upper Extremity Surgeon</p>
      </div>
      <div class="doctor">
        <h2 class="doctor-name">Ebo Dansu, M.D.</h2>
        <p class="doctor-title">Board Certified Hip &amp; Knee<br>Replacement/General Orthopaedic<br>Surgeon</p>
      </div>
    </div>

    <div class="brand">
      <span class="brand-name">RV Bone &amp; Vitality Center</span>
    </div>

    <div class="divider"></div>

    <ul class="contacts">
      <li><svg viewBox="0 0 16 16" aria-hidden="true"><path d="M3 1h3l1.5 4-2 1.3a9 9 0 0 0 4.2 4.2L11 8.5l4 1.5v3a2 2 0 0 1-2 2A12 12 0 0 1 1 3a2 2 0 0 1 2-2z"/></svg>954-218-4063</li>
      <li><svg viewBox="0 0 16 16" aria-hidden="true"><path d="M4 1h8v4H4zM1 6h14v7h-3v2H4v-2H1zm4 5v3h6v-3z"/></svg>954-582-7341</li>
      <li><svg viewBox="0 0 16 16" aria-hidden="true"><path d="M1 3h14v10H1zm1.5 1.5L8 9l5.5-4.5z"/></svg>info@myrvbonecare.example</li>
      <li><svg viewBox="0 0 16 16" aria-hidden="true"><circle cx="8" cy="8" r="7"/></svg>www.rvbonecare.example</li>
    </ul>

    <div class="address-band">
      <svg viewBox="0 0 700 92" preserveAspectRatio="none" aria-hidden="true">
        <polygon points="0,68 420,68 440,10 700,10 700,92 0,92" fill="var(--navy)"/>
      </svg>
      <address class="address">38517 North Willowmere Ave<br>Maple Hollow, FL 33990</address>
    </div>
  </section>

</body>
</html>
```